Hollow Thicket, a 3d voxel survival video game needs a card for gaming conventions

I am the lead developer for Hollow Thicket http://www.HollowThicket.example and need a business card to hand out at an indie gaming convention
The card would need to include the game name, website url, my name, position (Lead Developer), e-mail and phone number
The game is a 3d, voxel (with smooth terrain) based survival game with guns and wildlife. The main icon of the game would likely be a grizzly bear but I am willing to accept other designs too.
Attached is a media kit for the game with some images you can use but don't have to its just what little art I can provide. Anything on the website or from the video game can also be used. unrelated art can also be used.
Target Market(s)
Indie Developers/publishers at conferences
Industry/Entity Type
Games
Contact Information for Business Card
Name: Corin Waldrick
Position: Lead Developer
E-mail: Pale_Kettle@mailbox.example
Phone number: 555-372-1186

```html
<!DOCTYPE html>
<html lang="en">
<head>
<meta charset="UTF-8">
<title>Hollow Thicket – Business Card</title>
<link rel="stylesheet" href="https://fonts.googleapis.com/css2?family=Roboto:wght@400&family=Saira+Condensed:wght@600&display=swap">
<style>
  :root {
    --backdrop: #a9a6a8;
    --card-center: #ddd5bb;
    --card-mid: #a9a27f;
    --card-edge: #45452a;
    --brand-red: #8e2f24;
    --ink: #222220;
    --ink-soft: #3a3a34;
    --bear-light: #9a6a45;
    --bear-dark: #4e3220;
  }
  * { margin: 0; padding: 0; box-sizing: border-box; }
  html, body { width: 1200px; height: 1200px; overflow: hidden; }
  body { background: var(--backdrop); position: relative; font-family: "Roboto", Arial, sans-serif; }

  .card {
    position: absolute;
    width: 714px;
    height: 421px;
    background: radial-gradient(ellipse 62% 68% at 50% 48%, var(--card-center) 0%, var(--card-mid) 55%, var(--card-edge) 100%);
    overflow: hidden;
  }
  .card--front { left: 237px; top: 118px; }
  .card--back  { left: 229px; top: 643px; }

  .mascot-photo {
    position: absolute;
    left: 233px; top: 78px;
    width: 145px; height: 150px;
    border-radius: 45% 55% 20% 20%;
    background: radial-gradient(ellipse at 55% 35%, var(--bear-light) 0%, var(--bear-dark) 70%, rgba(78,50,32,0) 100%);
  }

  .brand-name {
    position: absolute;
    font-family: "Saira Condensed", "Arial Narrow", sans-serif;
    font-weight: 600;
    color: var(--brand-red);
    text-transform: uppercase;
    letter-spacing: 2px;
    white-space: nowrap;
  }
  .card--front .brand-name {
    left: 0; width: 100%;
    top: 222px;
    text-align: center;
    font-size: 58px;
    line-height: 56px;
  }
  .card--back .brand-name {
    left: 0; width: 100%;
    top: 108px;
    text-align: center;
    font-size: 54px;
    line-height: 60px;
  }

  .holder {
    position: absolute;
    right: 421px;
    top: 238px;
    text-align: right;
  }
  .holder__name {
    font-family: "Saira Condensed", "Arial Narrow", sans-serif;
    font-weight: 600;
    font-size: 29px;
    line-height: 32px;
    color: var(--ink);
  }
  .holder__role {
    font-size: 17px;
    line-height: 24px;
    color: var(--ink-soft);
  }

  .contact-list {
    position: absolute;
    left: 352px;
    top: 227px;
    list-style: none;
  }
  .contact-list li {
    display: flex;
    align-items: center;
    height: 24.5px;
    font-size: 18px;
    color: var(--ink);
  }
  .contact-list svg {
    width: 16px; height: 16px;
    margin-right: 21px;
    fill: var(--ink);
    flex: none;
  }
</style>
</head>
<body>

  <section class="card card--front">
    <div class="mascot-photo" role="img" aria-label="Photo of a roaring grizzly bear, the game's mascot"></div>
    <div class="brand-name">Hollow<br>Thicket</div>
  </section>

  <section class="card card--back">
    <div class="brand-name">Hollow Thicket</div>

    <div class="holder">
      <div class="holder__name">Corin Waldrick</div>
      <div class="holder__role">Lead Developer</div>
    </div>

    <ul class="contact-list">
      <li>
        <svg viewBox="0 0 16 16" aria-hidden="true"><path d="M2 5c0-2 2-3 6-3s6 1 6 3v1h-3V5H5v1H2z"/><path d="M4 7h8l2 6H2z"/><circle cx="8" cy="10" r="1.5" fill="#ddd5bb"/></svg>
        555-372-1186
      </li>
      <li>
        <svg viewBox="0 0 16 16" aria-hidden="true"><path d="M8 1a7 7 0 1 0 0 14A7 7 0 0 0 8 1zm0 1.5c.8 0 1.8 1.7 2.1 4.5H5.9C6.2 4.2 7.2 2.5 8 2.5zM2.6 7h2.3c0-1.5.3-2.9.8-3.9A5.6 5.6 0 0 0 2.6 7zm8.5 0h2.3a5.6 5.6 0 0 0-3.1-3.9c.5 1 .8 2.4.8 3.9zM2.6 9a5.6 5.6 0 0 0 3.1 3.9c-.5-1-.8-2.4-.8-3.9zm3.3 0c.3 2.8 1.3 4.5 2.1 4.5s1.8-1.7 2.1-4.5zm5.2 0c0 1.5-.3 2.9-.8 3.9A5.6 5.6 0 0 0 13.4 9z"/></svg>
        www.hollowthicket.example
      </li>
      <li>
        <svg viewBox="0 0 16 16" aria-hidden="true"><path d="M1 3h14v10H1zm1.5 1.5v.3L8 9l5.5-4.2v-.3zm0 2.2v4.8h11V6.7L8 11z"/></svg>
        Pale_Kettle@mailbox.example
      </li>
    </ul>
  </section>

</body>
</html>
```